Business Cards for a law firm

Business cards for our law firm. Use our silhoette logo and OAK PARTNERS - check our website (www.oakpartners.example)

Contact Information for Business Card

our silhouette logo, OAK PARTNERS, 800-555-0147, Dorian Pemberton, dorian@oakpartners.example

Requirements
Must have
• our silhouette logo, OAK PARTNERS, 800-555-0147, Dorian Pemberton, dorian@oakpartners.example

```html
<!DOCTYPE html>
<html lang="en">
<head>
<meta charset="utf-8">
<title>Oak Partners – Business Cards</title>
<link rel="stylesheet" href="https://fonts.googleapis.com/css2?family=Montserrat:wght@400;600;700&display=swap">
<style>
  :root {
    --navy: #24306b;
    --navy-deep: #1c2660;
    --navy-light: #2e3d85;
    --ink: #1b1f3a;
    --paper: #ffffff;
    --backdrop: #e9e7e2;
  }
  * { box-sizing: border-box; margin: 0; padding: 0; }
  html, body { width: 1200px; height: 931px; overflow: hidden; }
  body {
    background: var(--backdrop);
    font-family: "Montserrat", Arial, sans-serif;
    position: relative;
  }
  .card {
    position: absolute;
    left: 250px;
    width: 700px;
    height: 400px;
    border-radius: 22px;
    overflow: hidden;
    box-shadow: 0 6px 18px rgba(0,0,0,0.18);
  }
  /* Back side */
  .card-back {
    top: 40px;
    background: linear-gradient(135deg, var(--navy-light) 0%, var(--navy) 55%, var(--navy-deep) 100%);
  }
  .card-back .wordmark {
    position: absolute;
    right: 70px;
    top: 190px;
    color: var(--paper);
    font-weight: 600;
    font-size: 38px;
    letter-spacing: 5px;
  }
  /* Front side */
  .card-front {
    top: 491px;
    background: var(--paper);
  }
  .brand {
    position: absolute;
    left: 300px;
    top: 72px;
    display: flex;
    align-items: center;
    gap: 14px;
    color: var(--navy);
    font-weight: 600;
    font-size: 30px;
    letter-spacing: 4px;
  }
  .brand-dot {
    width: 38px; height: 38px;
    border-radius: 50%;
    background: var(--navy);
  }
  .divider {
    position: absolute;
    left: 56px;
    right: 56px;
    top: 228px;
    height: 2px;
    background: var(--navy);
  }
  .person {
    position: absolute;
    left: 56px;
    top: 162px;
  }
  .person-name {
    color: var(--navy);
    font-weight: 700;
    font-size: 32px;
    line-height: 1.1;
  }
  .person-role {
    color: var(--ink);
    font-size: 17px;
    margin-top: 2px;
  }
  .contacts {
    position: absolute;
    left: 56px;
    top: 248px;
    list-style: none;
  }
  .contacts li {
    display: flex;
    align-items: center;
    gap: 12px;
    color: var(--ink);
    font-size: 17px;
    line-height: 31px;
  }
  .contacts svg { width: 16px; height: 16px; fill: var(--navy); flex: none; }
  .address {
    position: absolute;
    right: 56px;
    top: 248px;
    text-align: left;
    color: var(--ink);
    font-size: 16px;
    line-height: 22px;
  }
  .band {
    position: absolute;
    left: 0; right: 0; bottom: 0;
    height: 20px;
    background: var(--navy);
  }
</style>
</head>
<body>
  <section class="card card-back" aria-label="Card back">
    <div class="wordmark">OAK PARTNERS</div>
  </section>

  <section class="card card-front" aria-label="Card front">
    <div class="brand"><span class="brand-dot"></span>OAK PARTNERS</div>

    <div class="person">
      <div class="person-name">Dorian Pemberton</div>
      <div class="person-role">Lawyer</div>
    </div>
    <div class="divider"></div>

    <ul class="contacts">
      <li>
        <svg viewBox="0 0 24 24" aria-hidden="true"><path d="M6.6 10.8a15.1 15.1 0 0 0 6.6 6.6l2.2-2.2a1 1 0 0 1 1-.25 11.4 11.4 0 0 0 3.6.57 1 1 0 0 1 1 1V20a1 1 0 0 1-1 1A17 17 0 0 1 3 4a1 1 0 0 1 1-1h3.5a1 1 0 0 1 1 1c0 1.25.2 2.45.57 3.6a1 1 0 0 1-.25 1z"/></svg>
        800-555-0147
      </li>
      <li>
        <svg viewBox="0 0 24 24" aria-hidden="true"><path d="M2 5h20v14H2z M3.5 6.5 12 13l8.5-6.5" /><path d="M2 5l10 8 10-8v1.6l-10 8-10-8z" fill="#fff"/></svg>
        dorian@oakpartners.example
      </li>
      <li>
        <svg viewBox="0 0 24 24" aria-hidden="true"><circle cx="12" cy="12" r="10"/><path d="M2 12h20M12 2c3 3 3 17 0 20M12 2c-3 3-3 17 0 20" stroke="#fff" stroke-width="1.4" fill="none"/></svg>
        www.oakpartners.example
      </li>
    </ul>

    <address class="address" style="font-style:normal">
      418 Harbor View Rd, #112<br>
      Millbrook, OH 439915
    </address>

    <div class="band"></div>
  </section>
</body>
</html>
```